Heron Loan Partners Business Card

We need a business card design for our mortgage servicing company. In addition to servicing the loans of homeowners, we help homeowners with purchasing their homes and any mortgage refinancing. We would like to see designs that use the colors in the logo attached below (gold-ish yellow and navy blue), and any other design you deem fit! The design should communicate a simpler life with smart mortgages provided by Heron.

```html
<!DOCTYPE html>
<html lang="en">
<head>
<meta charset="utf-8">
<title>Heron Loan Partners Business Card</title>
<link href="https://fonts.googleapis.com/css2?family=Open+Sans:wght@400;600;700&display=swap" rel="stylesheet">
<style>
  :root {
    --backdrop: #222222;
    --navy: #261f52;
    --gold: #e3b43a;
    --white: #ffffff;
  }
  * { margin: 0; padding: 0; box-sizing: border-box; }
  html, body {
    width: 1200px; height: 780px; overflow: hidden;
    background: var(--backdrop);
    font-family: "Open Sans", sans-serif;
  }
  .sheet {
    position: relative; width: 1200px; height: 780px;
    display: flex; align-items: center; justify-content: center; gap: 40px;
  }
  .card {
    position: relative; width: 540px; height: 310px;
    background: var(--navy);
    border-bottom: 5px solid var(--gold);
    box-shadow: 0 10px 24px rgba(0,0,0,0.55);
  }
  .brand {
    display: flex; align-items: center; gap: 12px;
    color: var(--gold); font-weight: 700; line-height: 1;
  }
  .brand-dot {
    border-radius: 50%; background: var(--gold); flex: none;
  }
  .card-front .brand {
    position: absolute; left: 50%; top: 50%;
    transform: translate(-50%, -50%);
    font-size: 72px;
  }
  .card-front .brand-dot { width: 26px; height: 26px; }
  .card-back .brand {
    position: absolute; left: 34px; top: 34px; font-size: 40px;
  }
  .card-back .brand-dot { width: 16px; height: 16px; }
  .contact {
    position: absolute; left: 34px; right: 30px; bottom: 28px;
    color: var(--white); font-size: 13px;
  }
  .person { display: flex; align-items: baseline; gap: 8px; margin-bottom: 10px; }
  .person-first { color: var(--gold); font-weight: 700; font-size: 28px; }
  .person-last { color: var(--white); font-weight: 700; font-size: 28px; }
  .person-role { color: var(--gold); font-size: 14px; margin-left: 6px; }
  .contact-row { display: flex; gap: 26px; margin-bottom: 6px; white-space: nowrap; }
  .label { color: var(--gold); font-weight: 600; margin-right: 3px; }
  .address { white-space: nowrap; }
</style>
</head>
<body>
  <main class="sheet">
    <section class="card card-front" aria-label="Card front">
      <div class="brand"><span class="brand-dot"></span>Heron</div>
    </section>

    <section class="card card-back" aria-label="Card back">
      <div class="brand"><span class="brand-dot"></span>Heron</div>
      <div class="contact">
        <p class="person">
          <span class="person-first">Lena</span>
          <span class="person-last">Varga</span>
          <span class="person-role">CEO</span>
        </p>
        <p class="contact-row">
          <span><span class="label">T:</span>(555) 214-3680</span>
          <span><span class="label">E:</span>info@website.com</span>
          <span><span class="label">W:</span>www.website.com</span>
        </p>
        <p class="address">1840 Lakeside Ave. Suite 300 Denton, TX 76201</p>
      </div>
    </section>
  </main>
</body>
</html>
```